Craft Beer Company

We need a web design for our Tampa based craft beer company that shows and tells what we are about and our products, up and coming beers, events and happenings. Must has a verify age by selecting yes or no to "are you 21 years or older.. have logos and product labels etc... currently have Plimtora.com a our website, thats under construction.
Reason: more time to be thorough
Target Market(s)
Craft Beer Enthusiasts , Craft Beer Community
Industry/Entity Type
Construction
Requirements
Must have
- The pages on the site should have, about us, events, our beer, store for e-commerce
being that we are set up with Plimtora.com I would like to contineu to use them, unless there is another option available. We have the domain there.

```html
<!DOCTYPE html>
<html lang="en">
<head>
<meta charset="utf-8">
<title>Harborline Beer Co</title>
<link href="https://fonts.googleapis.com/css2?family=Overlock:wght@400;700&family=Open+Sans:wght@400;600&display=swap" rel="stylesheet">
<style>
:root{
  --green-dark:#1d3a1d;
  --green-deep:#142a14;
  --green-lime:#8cc63f;
  --paper:#e9ede2;
  --modal:#e7e8cf;
  --ink:#2b2f26;
  --btn-no:#46452f;
  --shade:rgba(14,26,12,.62);
}
*{margin:0;padding:0;box-sizing:border-box}
html,body{width:717px;height:1200px;overflow:hidden}
body{position:relative;font-family:"Open Sans",sans-serif;background:var(--paper);color:var(--ink)}
.abs{position:absolute}
.heading{font-family:"Overlock",sans-serif;font-weight:400}

.topband{left:0;top:0;width:717px;height:35px;background:#dfe5d8}
.nav{left:0;top:35px;width:717px;height:27px;background:var(--green-dark);font-size:7px;letter-spacing:.6px;text-transform:uppercase;color:#d8e3cf}
.nav a{position:absolute;top:0;height:27px;line-height:27px;color:inherit;text-decoration:none}
.nav a.active{background:var(--green-lime);color:#173217;padding:0 10px}
.brand{left:322px;top:1px;width:74px;height:74px;border-radius:50%;background:var(--green-dark);border:3px solid var(--paper);display:flex;align-items:center;justify-content:center;text-align:center;font-family:"Overlock",sans-serif;font-size:10px;font-weight:700;color:#fff;line-height:1.1}

.hero{left:0;top:62px;width:717px;height:304px;background:
  radial-gradient(ellipse 60px 90px at 85px 220px,rgba(214,150,50,.85),rgba(214,150,50,0)),
  radial-gradient(ellipse 220px 80px at 600px 270px,rgba(150,120,60,.55),rgba(150,120,60,0)),
  linear-gradient(180deg,#3a4048 0%,#262a2c 55%,#1f211b 100%)}
.hero-arrow{top:208px;color:#cfd6c6;font-size:22px}

.welcome-title{left:0;top:386px;width:717px;text-align:center;font-size:17px;color:#2a3a22}
.welcome-text{left:66px;top:410px;width:585px;text-align:center;font-size:6.3px;line-height:15px;color:#4a5040}
.beers-title{left:0;top:470px;width:717px;text-align:center;font-size:16px;color:#2a3a22}
.beers{left:60px;top:502px;width:598px;height:100px;background:#fbfcf8;box-shadow:0 6px 6px -3px rgba(0,0,0,.5)}
.beer{position:absolute;top:0;width:195px;height:100px}
.beer .bottle{position:absolute;left:17px;top:0;width:22px;height:86px;border-radius:7px 7px 3px 3px;background:linear-gradient(90deg,#23200f,#5a4a24 45%,#2a2814)}
.beer h4{position:absolute;left:57px;top:14px;font-weight:400;font-size:8px;color:#333}
.beer hr{position:absolute;left:57px;top:32px;width:85px;border:0;border-top:1px solid #bbb}
.beer p{position:absolute;left:57px;top:42px;width:135px;font-size:6.4px;line-height:11px;color:#666}
.beer .more{position:absolute;left:57px;top:78px;font-size:6px;color:var(--green-lime)}
.car-arrow{top:538px;font-size:20px;color:#555}

.events{left:0;top:620px;width:717px;height:227px;background:var(--green-dark)}
.events-title{left:0;top:637px;width:717px;text-align:center;font-size:16px;color:#cfe1bf}
.event{position:absolute;top:669px;width:134px;height:153px;border:1px solid #4d6b3c}
.event .photo{height:94px}
.photo.crowd{background:radial-gradient(ellipse 70px 40px at 60% 60%,#5a5444,#262620 70%),#262620}
.photo.taproom{background:radial-gradient(ellipse 40px 60px at 25% 50%,#8a8c80,#2c2e28 70%),#2c2e28}
.photo.pour{background:radial-gradient(ellipse 60px 50px at 65% 45%,#9a6a48,#4a3420 70%),#4a3420}
.photo.glass{background:linear-gradient(90deg,#d9b860 0%,#e8e2cc 45%,#e8e2cc 60%,#6a4a24 100%)}
.event p{height:33px;padding:5px 8px;font-size:6.8px;line-height:12px;color:#cfd8c4;background:#2a4a26}
.event .bar{height:26px;background:var(--green-lime);display:flex;justify-content:space-between;align-items:center;padding:0 9px;font-size:6.8px;color:#1d3a1d}

.col-title{top:864px;font-size:15px;color:#2a3a22}
.feed{top:886px;width:184px;height:128px;border:1px solid #d0d6c8;background:#f6f8f2}
.item{position:absolute;left:14px;width:160px;font-size:6px;line-height:7px;color:#555}
.item .sq{position:absolute;left:0;top:0;width:20px;height:20px;background:var(--green-dark)}
.item span{display:block;margin-left:26px}
.item small{display:block;margin-left:26px;font-size:4.5px;color:#999}
.tw .sq{width:24px;height:24px;background:#5b9bc0}
.tw span{margin-left:32px}
.tw b{display:block;margin-left:32px;font-weight:400;font-size:7.5px;color:#777}
.tw small{margin-left:32px}
.upcoming{left:466px;top:870px;width:184px;height:144px;background:#23241c}
.upcoming h3{height:24px;line-height:24px;padding-left:12px;background:var(--green-lime);font-size:11px;color:#1d3a1d}
.upcoming .photo{height:120px;background:radial-gradient(ellipse 90px 50px at 50% 55%,#6e6450,#2a2a22 75%),#2a2a22}

.footer{left:0;top:1040px;width:717px;height:160px;background:var(--green-deep);color:#a9b89c;font-size:6.5px}
.footer .ft{top:14px;font-size:11px;color:#b9cca6}
.footer ul{list-style:none;line-height:15.5px}
.input{left:491px;top:1100px;width:159px;height:23px;background:#fff;color:#999;padding:7px 9px;font-size:6.5px}
.subscribe{left:491px;top:1128px;width:72px;height:20px;background:var(--green-lime);color:#1d3a1d;text-align:center;line-height:20px;font-size:6px}
.copy{left:0;top:1178px;width:717px;text-align:center;font-size:6.5px;color:#8a9a80}

.shade{left:0;top:0;width:717px;height:1200px;background:var(--shade)}
.modal{left:99px;top:73px;width:519px;height:284px;background:var(--modal);box-shadow:0 0 14px rgba(0,0,0,.5)}
.modal-art{position:absolute;left:0;top:0;width:300px;height:284px;background:
  radial-gradient(ellipse 110px 120px at 80px 90px,#7a5a3a,rgba(122,90,58,0) 100%),
  radial-gradient(ellipse 70px 80px at 150px 230px,#e0a030,rgba(224,160,48,0) 100%),
  radial-gradient(ellipse 90px 40px at 250px 230px,#d8a040,rgba(216,160,64,0) 100%),
  linear-gradient(90deg,#8a6a48 0%,#a07848 40%,rgba(231,232,207,0) 100%)}
.modal h2{position:absolute;left:214px;top:66px;width:264px;text-align:center;font-size:20px;color:#1c2a18;font-family:"Overlock",sans-serif;font-weight:700}
.modal p{position:absolute;left:222px;top:95px;width:262px;text-align:center;font-size:6.7px;line-height:15.3px;color:#3a3d2e}
.btn{position:absolute;top:164px;width:48px;height:23px;line-height:23px;text-align:center;font-size:8px;color:#fff}
.yes{left:304px;background:var(--green-lime)}
.no{left:360px;background:var(--btn-no)}
</style>
</head>
<body>

<div class="abs topband"></div>
<nav class="abs nav">
  <a class="active" style="left:66px">Home</a>
  <a style="left:126px">About Us</a>
  <a style="left:192px">Our Products</a>
  <a style="left:277px">Events</a>
  <a style="left:410px">News</a>
  <a style="left:460px">Blog</a>
  <a style="left:508px">Our Locations</a>
  <a style="left:596px">Contact Us</a>
</nav>
<div class="abs brand">Harborline<br>Beer Co</div>

<div class="abs hero" role="img" aria-label="Slider photo of beer glasses over a night city skyline"></div>
<div class="abs hero-arrow" style="left:18px">&#8249;</div>
<div class="abs hero-arrow" style="left:686px">&#8250;</div>

<h2 class="abs heading welcome-title">Welcome To Harborline Beer Co</h2>
<p class="abs welcome-text">Ut wisi enim ad minim veniam, quis nostrud exerci tation ullamcorper suscipit lobortis nisl ut aliquip ex ea commodo consequat. Duis autem vel eum iriure dolor in hendrerit in vulputate velit esse molestie consequat, vel illum dolore eu feugiat nulla facilisis at vero eros et accumsan et iusto odio dignissim qui blandit praesent luptatum zzril delenit augue duis dolore te feugait nulla facilisi. Nam liber tempor cum soluta nobis eleifend option congue nihil imperdiet doming id quod mazim placerat facer possim assum.</p>

<h2 class="abs heading beers-title">Upcoming Beers</h2>
<div class="abs car-arrow" style="left:38px">&#8249;</div>
<div class="abs car-arrow" style="left:670px">&#8250;</div>
<section class="abs beers">
  <article class="beer" style="left:0"><div class="bottle" role="img" aria-label="Beer bottle"></div><h4>Ut wisi enim ad minim</h4><hr><p>Lorem ipsum dolor sit amet, consec tetuer adipiscing elit, sed diam nonum lorem ipsum</p><span class="more">READ MORE</span></article>
  <article class="beer" style="left:195px"><div class="bottle" role="img" aria-label="Beer bottle"></div><h4>Ut wisi enim ad minim</h4><hr><p>Lorem ipsum dolor sit amet, consec tetuer adipiscing elit, sed diam nonum lorem ipsum</p><span class="more">READ MORE</span></article>
  <article class="beer" style="left:390px"><div class="bottle" role="img" aria-label="Beer bottle"></div><h4>Ut wisi enim ad minim</h4><hr><p>Lorem ipsum dolor sit amet, consec tetuer adipiscing elit, sed diam nonum lorem ipsum</p><span class="more">READ MORE</span></article>
</section>

<section class="abs events"></section>
<h2 class="abs heading events-title">Events &amp; Happenings</h2>
<article class="event" style="left:67px"><div class="photo crowd" role="img" aria-label="Group photo at a bar event"></div><p>Lorem ipsum dolor sit amet, consec tetuer adipiscing elit</p><div class="bar"><span>OCT 14,2014</span><span>READ MORE</span></div></article>
<article class="event" style="left:217px"><div class="photo taproom" role="img" aria-label="Tap room with a large bottle display"></div><p>Ut wisi enim ad minim veniam, quis nostrud exerci tation ullamcorper</p><div class="bar"><span>OCT 14,2014</span><span>READ MORE</span></div></article>
<article class="event" style="left:366px"><div class="photo pour" role="img" aria-label="Bartender pouring from a tap"></div><p>Lorem ipsum dolor sit amet, consec tetuer adipiscing elit</p><div class="bar"><span>OCT 14,2014</span><span>READ MORE</span></div></article>
<article class="event" style="left:516px"><div class="photo glass" role="img" aria-label="Glass of beer beside a bottle"></div><p>Ut wisi enim ad minim veniam, quis nostrud exerci tation ullamcorper</p><div class="bar"><span>OCT 14,2014</span><span>READ MORE</span></div></article>

<h3 class="abs heading col-title" style="left:66px">Chatterbook</h3>
<div class="abs feed" style="left:66px">
  <div class="item" style="top:10px"><i class="sq"></i><span>Lorem ipsum dolor sit amet, consectetuer adipiscing, sed diam nonummy nibh</span><small>8 people recommend this</small></div>
  <div class="item" style="top:41px"><i class="sq"></i><span>Lorem ipsum dolor sit amet, consectetuer adipiscing, sed diam nonummy nibh</span><small>5 people recommend this</small></div>
  <div class="item" style="top:72px"><i class="sq"></i><span>Lorem ipsum dolor sit amet, consectetuer adipiscing, sed diam nonummy nibh</span><small>3 people recommend this</small></div>
  <div class="item" style="top:110px"><span style="margin-left:0">&#9633; Chatterbook social plugin</span></div>
</div>

<h3 class="abs heading col-title" style="left:265px">Chirper</h3>
<div class="abs feed" style="left:265px">
  <div class="item tw" style="top:9px"><i class="sq"></i><b>Harborline Beer Co</b><span>Ut wisi enim ad minim veniam, quis nostrud exerci tation ullamcorper</span><small>2 days</small></div>
  <div class="item tw" style="top:51px"><i class="sq"></i><b>Harborline Beer Co</b><span>Ut wisi enim ad minim veniam...</span><small>4 days</small></div>
  <div class="item tw" style="top:89px"><i class="sq"></i><b>Harborline Beer Co</b><span>Typi non habent claritatem insitam</span><small>6 days</small></div>
</div>

<section class="abs upcoming"><h3 class="heading">Upcoming Events</h3><div class="photo" role="img" aria-label="Group photo from a brewery event"></div></section>

<footer class="abs footer">
  <div class="abs" style="left:68px;top:34px;line-height:12px">
    <div style="color:#d5e2c8">&#9679; CITY NAME</div>
    <div style="padding-left:12px">381 lorem ipsm lorem ipsm<br>lorem ipsm lorem 12768</div>
    <div style="margin-top:10px">&#9993; info@domainname.com</div>
    <div style="margin-top:10px">&#9742; +1.234.567.78900</div>
  </div>
  <h4 class="abs heading ft" style="left:234px">Quick Links</h4>
  <ul class="abs" style="left:235px;top:32px"><li>Home</li><li>Services</li><li>Products</li><li>About Us</li><li>Contact Us</li></ul>
  <h4 class="abs heading ft" style="left:350px">Social Networks</h4>
  <ul class="abs" style="left:352px;top:32px"><li>&#9632; Chatterbook</li><li>&#9632; Chirper</li><li>&#9632; Linkwork</li><li>&#9632; Searchplus</li><li>&#9632; RSS</li></ul>
  <h4 class="abs heading ft" style="left:491px">Newsletter Signup</h4>
  <p class="abs" style="left:491px;top:32px;width:159px;line-height:12px;color:#6f7f64">Enter your email address to receive our latest newsletters containing our latest news.</p>
</footer>
<div class="abs input">Email Address</div>
<div class="abs subscribe">SUBSCRIBE</div>
<div class="abs copy">&copy;2014 Harborline Beer Co. &nbsp;<span style="color:#b7c6aa">Privacy Policy</span> &nbsp;|&nbsp; <span style="color:#b7c6aa">Terms of Service</span></div>

<div class="abs shade"></div>

<div class="abs modal" role="dialog" aria-label="Age verification">
  <div class="modal-art" role="img" aria-label="Wooden barrel with beer bottles, full glasses and wheat"></div>
  <h2>ARE YOU 21 YEARS OR OLDER</h2>
  <p>Ut wisi enim ad minim veniam, quis nostrud exerci tation ullamcorper suscipit lobortis nisl ut aliquip ex ea commodo consequat. Duis autem vel eum iriure dolor in hendrerit in vulputate velit esse molestie consequat, vel illum dolore eu feugiat nulla facilisis at vero eros et accumsan et iusto odio dignissim.</p>
  <div class="btn yes">YES</div>
  <div class="btn no">NO</div>
</div>

</body>
</html>
```